QVR business card

Need a business card for a company that provides instructional design and elearning development services. The website is here: http://quorvane.studio/

I'm attaching a current logo, as well as the old business card design. While I like to keep it clean, the old design is too simplistic for my liking. The only idea I want to reuse from the old design is placing industry jargon on the back of the card, just need a better way to present it. But if you have other ideas for the back--feel free to experiment.

Please use the colors complementary to the color we have on the website. Thank you!

```html
<!DOCTYPE html>
<html lang="en">
<head>
<meta charset="utf-8">
<title>QVR business card</title>
<link href="https://fonts.googleapis.com/css2?family=Lato:wght@400;700&family=Oswald:wght@400;500&display=swap" rel="stylesheet">
<style>
  :root {
    --page: #e8e5e0;
    --white: #ffffff;
    --teal: #17b1ae;
    --teal-light: #6fd3c2;
    --teal-dark: #12918f;
    --ink: #3a3a3a;
    --shadow: rgba(0, 0, 0, 0.18);
  }
  * { margin: 0; padding: 0; box-sizing: border-box; }
  html, body { width: 1200px; height: 1120px; overflow: hidden; background: var(--page); }
  .canvas { position: relative; width: 1200px; height: 1120px; }

  .card {
    position: absolute; left: 160px; width: 880px; height: 503px;
    overflow: hidden; box-shadow: 0 6px 18px var(--shadow);
  }
  .card-front { top: 37px; background: var(--white); }
  .card-back { top: 580px; background: var(--teal); }

  /* front */
  .brand {
    position: absolute; top: 70px; left: 0; width: 100%;
    display: flex; justify-content: center; align-items: center; gap: 18px;
  }
  .brand-mark { width: 46px; height: 46px; background: var(--teal); }
  .brand-name {
    font-family: "Lato", sans-serif; font-weight: 700; font-size: 84px;
    letter-spacing: 4px; color: var(--teal); line-height: 1;
  }
  .person { position: absolute; top: 220px; width: 100%; text-align: center; font-family: "Lato", sans-serif; }
  .person-name { font-size: 30px; font-weight: 700; color: var(--teal); letter-spacing: 0.5px; }
  .person-title { font-size: 30px; font-weight: 700; color: var(--ink); margin-top: 4px; }

  .contact-band { position: absolute; left: 0; bottom: 0; width: 880px; height: 150px; }
  .contact-band svg { position: absolute; inset: 0; }
  .contact-item {
    position: absolute; bottom: 36px; font-family: "Lato", sans-serif;
    font-size: 21px; color: var(--white); text-align: center; width: 290px;
  }
  .contact-phone { left: 10px; }
  .contact-email { left: 295px; }
  .contact-web { left: 580px; }

  /* back */
  .help-title {
    position: absolute; left: 64px; top: 62px;
    font-family: "Oswald", sans-serif; font-weight: 400; font-size: 100px;
    line-height: 1.0; color: var(--white); text-transform: uppercase;
  }
  .service-rail { position: absolute; left: 360px; top: 40px; width: 90px; height: 430px; }
  .service-list {
    position: absolute; left: 470px; top: 53px; list-style: none;
    font-family: "Oswald", sans-serif; font-weight: 500; font-size: 31px;
    color: var(--white); letter-spacing: 1px; text-transform: uppercase;
  }
  .service-list li { height: 70px; line-height: 46px; white-space: nowrap; }
</style>
</head>
<body>
<main class="canvas">

  <section class="card card-front" aria-label="Card front">
    <div class="brand">
      <span class="brand-mark"></span>
      <span class="brand-name">QVR</span>
    </div>
    <div class="person">
      <p class="person-name">Marten Holloway</p>
      <p class="person-title">Managing Director</p>
    </div>
    <div class="contact-band">
      <svg viewBox="0 0 880 150" width="880" height="150" aria-hidden="true">
        <defs>
          <linearGradient id="bandFill" x1="0" y1="1" x2="0" y2="0">
            <stop offset="0" stop-color="#17b1ae"/>
            <stop offset="1" stop-color="#6fd3c2"/>
          </linearGradient>
        </defs>
        <path d="M0 70 L105 70 L120 22 L180 22 L195 70 L405 70 L420 22 L480 22 L495 70 L705 70 L720 22 L780 22 L795 70 L880 70 L880 150 L0 150 Z" fill="url(#bandFill)"/>
        <!-- phone -->
        <g transform="translate(150 45)" fill="none" stroke="#fff" stroke-width="2.4">
          <circle r="12"/>
          <path d="M-4 -6 q-1 8 6 12 l2 -2 -3 -3 -1 1 q-2 -2 -2 -5 l1 -1 -2 -3 z" fill="#fff" stroke="none"/>
        </g>
        <!-- envelope -->
        <g transform="translate(450 45)" fill="none" stroke="#fff" stroke-width="2.4">
          <rect x="-13" y="-9" width="26" height="18" rx="2"/>
          <path d="M-13 -9 L0 2 L13 -9"/>
        </g>
        <!-- globe -->
        <g transform="translate(750 45)" fill="none" stroke="#fff" stroke-width="2.2">
          <circle r="12"/>
          <ellipse rx="5" ry="12"/>
          <path d="M-12 0 H12 M-10 -6 H10 M-10 6 H10"/>
        </g>
      </svg>
      <p class="contact-item contact-phone">555-014-2288</p>
      <p class="contact-item contact-email">mholloway@quorvane.studio</p>
      <p class="contact-item contact-web">www.quorvane.studio</p>
    </div>
  </section>

  <section class="card card-back" aria-label="Card back">
    <h1 class="help-title">How<br>can<br>we<br>help?</h1>

    <svg class="service-rail" viewBox="0 0 90 430" width="90" height="430" aria-hidden="true">
      <g fill="none" stroke="#fff" stroke-width="2.2">
        <path d="M45 56 V84 M45 126 V154 M45 196 V224 M45 266 V294 M45 336 V364"/>
        <path d="M45 14 L85 35 L45 56 L5 35 Z"/>
        <path d="M45 84 L85 105 L45 126 L5 105 Z"/>
        <path d="M45 154 L85 175 L45 196 L5 175 Z"/>
        <path d="M45 224 L85 245 L45 266 L5 245 Z"/>
        <path d="M45 294 L85 315 L45 336 L5 315 Z"/>
        <path d="M45 364 L85 385 L45 406 L5 385 Z"/>
        <rect x="39" y="26" width="12" height="18" rx="2"/>
        <rect x="35" y="98" width="20" height="13"/>
        <path d="M39 170 l-5 5 5 5 M51 170 l5 5 -5 5"/>
        <circle cx="45" cy="242" r="6"/>
        <path d="M42 250 H48"/>
        <circle cx="45" cy="313" r="7"/>
        <path d="M45 306 V300 M38 313 H33 M52 313 H57"/>
        <rect x="34" y="377" width="22" height="14"/>
        <path d="M45 391 V395 M40 395 H50"/>
      </g>
    </svg>

    <ul class="service-list">
      <li>Mobile Learning SCORM</li>
      <li>Instructional Design LMS</li>
      <li>MOOCs eLearning HTML5</li>
      <li>Adult Learning Theory</li>
      <li>Gamification Classroom</li>
      <li>xAPI Blended Learning</li>
    </ul>
  </section>

</main>
</body>
</html>
```